Wine bottle label design for Coral Hollow Winery

We need a label design for our wine that is being sold in St. John, USVI. We want it to be classic looking, a wine to be taken seriously. Not a whimsical Caribbean design with palm trees and beaches and waves... you get it. The story is about me, my dad and brother making wine for the past 12 years. We're of Italian heritage, so most of the grape varietals will reflect that (No, I don't want any images of Italy on the label :). The price point will be $22-25 retail, so the label should represent that. I have attached what I "threw together" for front/back. I like a simple clean look, black on white background, maybe with another rich accent color (I used hunter green). The back of the label will have a pic of me, my dad and brother. Aside from the "story" and the gov't warning, the design is open for interpretation.
Updates

Reason: Would like to see more designs different from the sample design I did and posted here.

Target Market(s)

Vistors and locals on the island of St. John who drink wine!

Font styles to use
Serif
Sans Serif

Requirements
Must have
• An upscale, but warm and inviting look and feel. Include logo in label design (Attached).
Nice to have
• It's okay if it's an all front label (See attached sample)
Should not have
• Palm trees, coconuts, waves, pictures grapes, vineyards, or leaves.

```html
<!DOCTYPE html>
<html lang="en">
<head>
<meta charset="utf-8">
<title>Coral Hollow Winery – Sangiovese Cabernet Label</title>
<link href="https://fonts.googleapis.com/css2?family=Libre+Baskerville:wght@400;700&family=Crimson+Text:wght@400;600&display=swap" rel="stylesheet">
<style>
  :root {
    --paper: #ffffff;
    --ink: #1c2a20;
    --hunter: #2f6b3a;
    --hunter-soft: #7fae86;
    --rule: #9aa59c;
    --edge: #dedede;
  }
  html, body {
    margin: 0;
    padding: 0;
    overflow: hidden;
    background: var(--paper);
  }
  .label {
    position: relative;
    width: 813px;
    height: 1200px;
    box-sizing: border-box;
    border: 2px solid var(--edge);
    background: var(--paper);
    color: var(--ink);
    font-family: "Crimson Text", Georgia, serif;
    text-align: center;
    overflow: hidden;
  }
  .winery-name {
    position: absolute;
    top: 70px;
    left: 0;
    right: 0;
    margin: 0;
    font-family: "Libre Baskerville", Georgia, serif;
    font-weight: 400;
    font-size: 34px;
    letter-spacing: 6px;
    line-height: 1.5;
    color: var(--ink);
  }
  .varietal {
    position: absolute;
    top: 212px;
    left: 0;
    right: 0;
    margin: 0;
    font-size: 42px;
    font-weight: 400;
    color: var(--hunter);
  }
  .place {
    position: absolute;
    top: 272px;
    left: 0;
    right: 0;
    margin: 0;
    font-family: "Libre Baskerville", Georgia, serif;
    font-weight: 700;
    font-size: 58px;
    letter-spacing: 1px;
    color: var(--ink);
  }
  .divider {
    position: absolute;
    top: 366px;
    left: 120px;
    right: 120px;
    height: 0;
    border-top: 2px solid var(--rule);
  }
  .vintage-mark {
    position: absolute;
    top: 420px;
    left: 50%;
    width: 360px;
    height: 360px;
    margin-left: -180px;
  }
  .vintage-year {
    position: absolute;
    top: 568px;
    left: 0;
    right: 0;
    margin: 0;
    font-size: 40px;
    font-weight: 600;
    color: var(--hunter);
  }
  .fine-print {
    position: absolute;
    bottom: 58px;
    left: 90px;
    right: 90px;
    display: flex;
    justify-content: space-between;
    font-size: 20px;
    color: var(--ink);
  }
</style>
</head>
<body>
  <main class="label">
    <p class="winery-name">CORAL HOLLOW<br>WINERY</p>

    <h2 class="varietal">Sangiovese - Cabernet</h2>
    <h1 class="place">ST. JOHN, USVI</h1>
    <div class="divider"></div>

    <svg class="vintage-mark" viewBox="0 0 360 360" role="img" aria-label="Circular green scroll ornament framing the vintage year">
      <defs>
        <radialGradient id="ornamentTone" cx="50%" cy="50%" r="50%">
          <stop offset="0%" stop-color="#ffffff"/>
          <stop offset="45%" stop-color="#ffffff"/>
          <stop offset="60%" stop-color="#cfe3d1"/>
          <stop offset="80%" stop-color="#7fae86"/>
          <stop offset="100%" stop-color="#ffffff" stop-opacity="0"/>
        </radialGradient>
      </defs>
      <circle cx="180" cy="180" r="180" fill="url(#ornamentTone)"/>
    </svg>
    <p class="vintage-year">2014</p>

    <div class="fine-print">
      <span class="volume">750 ml</span>
      <span class="style">Red Table Wine</span>
      <span class="alcohol">alc. 13% vol</span>
    </div>
  </main>
</body>
</html>
```